A design led business card for the construction industry

High-end business card to match logo. White logo on dark grey/off black to the front. Matching dark font on white to back, possibly with logo design again.

We offer construction and project management services to commercial and private clients in the UK. Projetcs range from newbuilds, conversion of listed buildings and refurbishments and extensions of existing homes. Our focus is on quality and attention to detail using the highest skills.

Contact Information for Business Card

Name; Dorian Keble BSc
Position; Project Manager
Mobile; 07962 408 175
Tel; 01632 960457
email; dorian@stonevale.co.uk
web; www.stonevale.co.uk
Address; Kelbridge on Arne, KX4 7PW

Colors

Designer to choose only greyscale colors for use in the design.

Requirements
Must have
• To include the below description of the business,

CONSTRUCTION - PROJECT MANAGEMENT
Nice to have
• The posibility of the top back of the card being used as a ruler. So will have a measurement to scale in mm or an architect scale of 1:50
Should not have
• Should not be portrait

```html
<!DOCTYPE html>
<html lang="en">
<head>
<meta charset="utf-8">
<title>Stonevale – Business Card Front</title>
<link rel="stylesheet" href="https://fonts.googleapis.com/css2?family=Arimo:wght@400;700&display=swap">
<style>
  :root {
    --canvas-bg: #e4e2e1;
    --card-bg: #2b2b2d;
    --card-text: #ffffff;
    --badge-light: #f7f5f5;
    --badge-mid: #dcd6d6;
    --badge-edge: #c9c2c2;
    --badge-text: #1c1c1c;
    --badge-subtext: #2f2f2f;
  }
  * { box-sizing: border-box; margin: 0; padding: 0; }
  html, body {
    width: 1200px;
    height: 900px;
    overflow: hidden;
  }
  body {
    background: var(--canvas-bg);
    font-family: "Arimo", Arial, sans-serif;
    position: relative;
  }
  .card {
    position: absolute;
    left: 100px;
    top: 141px;
    width: 1000px;
    height: 617px;
    background: var(--card-bg);
    color: var(--card-text);
    box-shadow: 0 10px 30px rgba(0,0,0,0.18);
  }
  .identity {
    position: absolute;
    left: 49px;
    top: 70px;
  }
  .identity__name {
    font-size: 37px;
    font-weight: 700;
    letter-spacing: 0.2px;
    line-height: 1.1;
    white-space: nowrap;
  }
  .identity__credential {
    font-weight: 400;
  }
  .identity__role {
    font-size: 29px;
    font-weight: 400;
    margin-top: 2px;
    letter-spacing: 0.3px;
  }
  .contact-list {
    position: absolute;
    left: 49px;
    top: 325px;
    list-style: none;
  }
  .contact-list__item {
    display: flex;
    align-items: center;
    height: 36px;
    font-size: 28px;
    letter-spacing: 0.3px;
    white-space: nowrap;
  }
  .contact-list__icon {
    width: 26px;
    height: 26px;
    margin-right: 10px;
    flex-shrink: 0;
  }
  .address {
    position: absolute;
    left: 54px;
    top: 502px;
    font-size: 28px;
    letter-spacing: 0.3px;
    white-space: nowrap;
  }
  .badge {
    position: absolute;
    left: 434px;
    top: 58px;
    width: 500px;
    height: 500px;
    border-radius: 50%;
    background: radial-gradient(circle at 45% 40%, var(--badge-light) 0%, var(--badge-mid) 70%, var(--badge-edge) 100%);
    color: var(--badge-text);
    text-align: center;
  }
  .badge__name {
    position: absolute;
    left: 0;
    right: 0;
    top: 290px;
    font-size: 31px;
    font-weight: 400;
    letter-spacing: 14px;
    padding-left: 14px;
  }
  .badge__tagline {
    position: absolute;
    left: 0;
    right: 0;
    top: 356px;
    font-size: 25px;
    line-height: 32px;
    color: var(--badge-subtext);
    letter-spacing: 0.3px;
  }
</style>
</head>
<body>
  <section class="card">
    <header class="identity">
      <h1 class="identity__name">DORIAN KEBLE <span class="identity__credential">BSc</span></h1>
      <p class="identity__role">Project Manager</p>
    </header>

    <ul class="contact-list">
      <li class="contact-list__item">
        <svg class="contact-list__icon" viewBox="0 0 24 24" aria-hidden="true">
          <rect x="6" y="1.5" width="12" height="21" rx="2" fill="none" stroke="currentColor" stroke-width="2"/>
          <line x1="6" y1="17.5" x2="18" y2="17.5" stroke="currentColor" stroke-width="1.6"/>
          <circle cx="12" cy="20" r="0.9" fill="currentColor"/>
        </svg>
        07962 408 175
      </li>
      <li class="contact-list__item">
        <svg class="contact-list__icon" viewBox="0 0 24 24" aria-hidden="true">
          <path d="M6.5 2.5l3 4-2 2.2c1.2 2.8 3.2 4.9 6 6.2l2.2-2 4 3-1.8 3.3c-.4.7-1.2 1-2 .8C9.4 18.3 5.6 14.5 3.9 7.6c-.2-.8.1-1.6.8-2z" fill="none" stroke="currentColor" stroke-width="1.8" stroke-linejoin="round"/>
          <path d="M14 3.5a7 7 0 0 1 6.5 6.5M14 7a3.5 3.5 0 0 1 3 3" fill="none" stroke="currentColor" stroke-width="1.6" stroke-linecap="round"/>
        </svg>
        01632 960457
      </li>
      <li class="contact-list__item">
        <svg class="contact-list__icon" viewBox="0 0 24 24" aria-hidden="true">
          <rect x="1.5" y="5" width="21" height="14" fill="currentColor"/>
          <path d="M2 5.5l10 8 10-8M2 18.5l7.5-6.5M22 18.5l-7.5-6.5" fill="none" stroke="#2b2b2d" stroke-width="1.4"/>
        </svg>
        dorian@stonevale.co.uk
      </li>
      <li class="contact-list__item">
        <svg class="contact-list__icon" viewBox="0 0 24 24" aria-hidden="true">
          <g fill="none" stroke="currentColor" stroke-width="1.5">
            <circle cx="12" cy="12" r="10"/>
            <ellipse cx="12" cy="12" rx="4.5" ry="10"/>
            <line x1="2" y1="12" x2="22" y2="12"/>
            <path d="M4 6.5h16M4 17.5h16"/>
          </g>
        </svg>
        www.stonevale.co.uk
      </li>
    </ul>

    <p class="address">Kelbridge on Arne, KX4 7PW</p>

    <div class="badge">
      <p class="badge__name">STONEVALE</p>
      <p class="badge__tagline">CONSTRUCTION<br>PROJECT MANAGEMENT</p>
    </div>
  </section>
</body>
</html>
```